Web design

We need the design for the logo and website for a women fashion website. No coding required. The colors used should be neutral (maybe with a light touch of color), the style should be modern, slightly luxurious, not too crowded. The target market is young professionals who love trendy clothes.
Updates

Need extra days to review

Target Market(s)

Young professionals

Industry/Entity Type

Apparel

Number of Pages Required

5+ page

Font styles to use
Sans Serif
Other font styles liked:
• Montserrat, Engravers Gothic, Benton Sans, gotham-book

Colors

Designer to choose colors to be used in the design.

```html
<!DOCTYPE html>
<html lang="en">
<head>
<meta charset="utf-8">
<title>LUNE — All Clothing</title>
<link href="https://fonts.googleapis.com/css2?family=Montserrat:wght@400;500;600;700&family=Cormorant+Garamond:wght@500;600&display=swap" rel="stylesheet">
<style>
:root{
  --ink:#1d1d1d;
  --muted:#8a8a8a;
  --line:#e6e6e6;
  --gold:#d9b35a;
  --sale:#d8342c;
  --hero:#e7e5e2;
  --strip:#f5ecea;
  --news:#eadfcf;
  --foot:#f6f6f6;
  --white:#ffffff;
}
*{box-sizing:border-box;margin:0;padding:0}
html,body{width:1200px;height:3232px;overflow:hidden}
body{font-family:"Montserrat",sans-serif;color:var(--ink);background:var(--white);position:relative}

/* header */
.site-header{height:80px;display:flex;align-items:center;justify-content:space-between;padding:0 100px;position:relative}
.main-nav{display:flex;gap:28px;font-size:13px;font-weight:500}
.main-nav .sale{color:var(--sale)}
.brand{position:absolute;left:50%;top:50%;transform:translate(-50%,-50%)}
.brand-name{font-family:"Montserrat",sans-serif;font-weight:600;font-size:26px;letter-spacing:4px;line-height:1;color:var(--ink)}
.header-tools{display:flex;align-items:center;gap:18px;font-size:12px;font-weight:500}
.header-tools svg{width:18px;height:18px;stroke:var(--ink);fill:none;stroke-width:1.6}

/* hero */
.hero{position:relative;height:440px;background:var(--hero);overflow:hidden}
.hero-photo{position:absolute;right:150px;top:0;width:560px;height:440px;background:linear-gradient(100deg,#d9d4cd 0%,#2f5a4c 30%,#c8b8a4 55%,#8c7966 80%,#d8d2ca 100%)}
.hero-copy{position:absolute;left:100px;top:140px;width:380px}
.hero-copy h1{font-family:"Cormorant Garamond",serif;font-weight:600;font-size:44px;letter-spacing:1px;margin-bottom:14px}
.hero-copy p{font-size:12px;line-height:1.6;color:#444}

/* perks */
.perks{height:60px;background:var(--strip);display:flex;align-items:center;justify-content:space-between;padding:0 150px;font-size:12px;font-weight:500}
.perk{display:flex;align-items:center;gap:10px}
.perk svg{width:20px;height:20px;stroke:var(--ink);fill:none;stroke-width:1.5}

/* products */
.popular{padding:0 100px;position:absolute;top:680px;left:0;width:1200px}
.section-head{display:flex;justify-content:space-between;align-items:center;margin-bottom:34px}
.section-head h2{font-size:26px;font-weight:700}
.sort{font-size:12px;color:#555}
.grid{display:grid;grid-template-columns:repeat(4,238px);column-gap:16px;row-gap:34px}
.card{height:398px}
.card-photo{height:316px;position:relative}
.badge{position:absolute;right:8px;bottom:10px;background:var(--white);font-size:9px;font-weight:600;padding:3px 6px}
.card-name{display:flex;justify-content:space-between;margin-top:10px;font-size:13px;font-weight:600}
.card-name svg{width:13px;height:13px;stroke:var(--ink);fill:none;stroke-width:1.6}
.card-desc{font-size:11px;color:var(--muted);margin-top:5px}
.card-price{display:flex;justify-content:space-between;align-items:center;margin-top:8px}
.card-price b{font-size:17px;font-weight:700}
.swatches{display:flex;gap:5px}
.swatches i{width:9px;height:9px;border-radius:50%;display:block}
.load-more{position:absolute;top:2480px;left:50%;transform:translateX(-50%);width:130px;height:38px;border:1.5px solid var(--gold);border-radius:20px;display:flex;align-items:center;justify-content:center;font-size:11px;font-weight:600;letter-spacing:1px;color:#b08c3c}

/* newsletter */
.newsletter{position:absolute;top:2620px;left:0;width:1200px;height:272px;background:var(--news);text-align:center;padding-top:72px}
.newsletter h2{font-size:34px;font-weight:600}
.newsletter p{font-size:12px;color:#666;margin-top:10px}
.signup{display:flex;justify-content:center;margin-top:22px}
.signup span{width:230px;height:42px;background:var(--white);font-size:12px;color:#999;display:flex;align-items:center;padding-left:16px;text-align:left}
.signup b{width:230px;height:42px;background:var(--ink);color:var(--white);font-size:12px;font-weight:600;display:flex;align-items:center;justify-content:center;letter-spacing:1px}

/* footer */
.site-footer{position:absolute;top:2892px;left:0;width:1200px;height:340px;background:var(--foot)}
.footer-brand{position:absolute;left:140px;top:110px}
.footer-brand .brand-name{font-size:44px;letter-spacing:6px}
.footer-col{position:absolute;top:82px;font-size:12px;color:#555}
.footer-col h3{font-size:13px;font-weight:700;color:var(--ink);letter-spacing:1px;margin-bottom:14px}
.footer-col li{list-style:none;margin-bottom:10px}
.social li{display:flex;align-items:center;gap:10px}
.social li i{width:12px;height:12px;border-radius:50%;background:#555;display:block}
.legal{position:absolute;bottom:0;left:100px;width:1000px;height:60px;border-top:1px solid var(--line);font-size:11px;color:#666;display:flex;align-items:center;justify-content:center}
</style>
</head>
<body>

<header class="site-header">
  <nav class="main-nav">
    <span>Latest Arrivals</span><span>Clothes ▾</span><span>LUNE Club</span><span class="sale">On Sale</span>
  </nav>
  <div class="brand"><span class="brand-name">LUNE</span></div>
  <div class="header-tools">
    <svg viewBox="0 0 20 20"><circle cx="8.5" cy="8.5" r="6"/><path d="M13 13l5 5"/></svg>
    <span>ENG ▾</span>
    <svg viewBox="0 0 20 20"><path d="M10 17s-7-4.3-7-9a4 4 0 0 1 7-2.5A4 4 0 0 1 17 8c0 4.7-7 9-7 9z"/></svg>
    <svg viewBox="0 0 20 20"><circle cx="10" cy="6.5" r="3.5"/><path d="M3 18c1-4 4-5.5 7-5.5s6 1.5 7 5.5"/></svg>
    <svg viewBox="0 0 20 20"><path d="M4 7h12l-1 11H5z"/><path d="M7 7a3 3 0 0 1 6 0"/></svg>
  </div>
</header>

<section class="hero">
  <div class="hero-photo" role="img" aria-label="Two women modelling tailored jackets against a light grey backdrop"></div>
  <div class="hero-copy">
    <h1>ALL CLOTHING</h1>
    <p>Modern pieces cut for busy days and easy evenings. Discover tailored jackets, soft knits and dresses made to move with you, in calm tones that pair with everything.</p>
  </div>
</section>

<section class="perks">
  <div class="perk"><svg viewBox="0 0 20 20"><circle cx="10" cy="10" r="8"/><path d="M2 10h16M10 2c3 3 3 13 0 16M10 2c-3 3-3 13 0 16"/></svg>Shipping Worldwide</div>
  <div class="perk"><svg viewBox="0 0 20 20"><path d="M1 5h11v9H1zM12 8h4l3 3v3h-7z"/><circle cx="5" cy="15" r="1.6"/><circle cx="15" cy="15" r="1.6"/></svg>Free Shipping On Orders Greater Than X$</div>
  <div class="perk"><svg viewBox="0 0 20 20"><path d="M4 10a6 6 0 1 0 2-4.5"/><path d="M3 3v4h4"/></svg>30 Days Return Policy</div>
</section>

<section class="popular">
  <div class="section-head"><h2>Popular Items</h2><span class="sort">⇅ Sort</span></div>
  <div class="grid">
    <article class="card"><div class="card-photo" role="img" aria-label="Model in a white knit sweater dress" style="background:linear-gradient(160deg,#d8d2cc,#f1ede8 50%,#c9c0b7)"><span class="badge">20% OFF</span></div><div class="card-name">Product Name<svg viewBox="0 0 20 20"><path d="M10 17s-7-4.3-7-9a4 4 0 0 1 7-2.5A4 4 0 0 1 17 8c0 4.7-7 9-7 9z"/></svg></div><p class="card-desc">Lorem ipsum dolor sit amet</p><div class="card-price"><b>$32.99</b><span class="swatches"><i style="background:#1d1d1d"></i><i style="background:#c9a27a"></i><i style="background:#d8d8d8"></i></span></div></article>
    <article class="card"><div class="card-photo" role="img" aria-label="Model in a burgundy fitted dress" style="background:linear-gradient(160deg,#d7cfc7,#7a2431 50%,#cfc5bb)"></div><div class="card-name">Product Name<svg viewBox="0 0 20 20"><path d="M10 17s-7-4.3-7-9a4 4 0 0 1 7-2.5A4 4 0 0 1 17 8c0 4.7-7 9-7 9z"/></svg></div><p class="card-desc">Lorem ipsum dolor sit amet</p><div class="card-price"><b>$32.99</b><span class="swatches"><i style="background:#1d1d1d"></i><i style="background:#7a2431"></i><i style="background:#d8d8d8"></i></span></div></article>
    <article class="card"><div class="card-photo" role="img" aria-label="Model in a brown polka dot top" style="background:linear-gradient(160deg,#c99e6e,#6b3a22 55%,#b98b5e)"></div><div class="card-name">Product Name<svg viewBox="0 0 20 20"><path d="M10 17s-7-4.3-7-9a4 4 0 0 1 7-2.5A4 4 0 0 1 17 8c0 4.7-7 9-7 9z"/></svg></div><p class="card-desc">Lorem ipsum dolor sit amet</p><div class="card-price"><b>$32.99</b><span class="swatches"><i style="background:#1d1d1d"></i><i style="background:#6b3a22"></i><i style="background:#d8d8d8"></i></span></div></article>
    <article class="card"><div class="card-photo" role="img" aria-label="Model in a cream satin lounge set" style="background:linear-gradient(160deg,#e2dcd6,#f4efe9 50%,#cfc6bd)"><span class="badge">NEW</span></div><div class="card-name">Product Name<svg viewBox="0 0 20 20"><path d="M10 17s-7-4.3-7-9a4 4 0 0 1 7-2.5A4 4 0 0 1 17 8c0 4.7-7 9-7 9z"/></svg></div><p class="card-desc">Lorem ipsum dolor sit amet</p><div class="card-price"><b>$32.99</b><span class="swatches"><i style="background:#1d1d1d"></i><i style="background:#e8dccd"></i><i style="background:#d8d8d8"></i></span></div></article>

    <article class="card"><div class="card-photo" role="img" aria-label="Model in a patterned brown wrap dress" style="background:linear-gradient(160deg,#5a3a2c,#8d6248 50%,#3e2a22)"><span class="badge">20% OFF</span></div><div class="card-name">Product Name<svg viewBox="0 0 20 20"><path d="M10 17s-7-4.3-7-9a4 4 0 0 1 7-2.5A4 4 0 0 1 17 8c0 4.7-7 9-7 9z"/></svg></div><p class="card-desc">Lorem ipsum dolor sit amet</p><div class="card-price"><b>$32.99</b><span class="swatches"><i style="background:#1d1d1d"></i><i style="background:#8d6248"></i><i style="background:#d8d8d8"></i></span></div></article>
    <article class="card"><div class="card-photo" role="img" aria-label="Model in a white dress with black dots" style="background:linear-gradient(160deg,#dcd6cf,#f2f0ed 50%,#bdb5ad)"></div><div class="card-name">Product Name<svg viewBox="0 0 20 20"><path d="M10 17s-7-4.3-7-9a4 4 0 0 1 7-2.5A4 4 0 0 1 17 8c0 4.7-7 9-7 9z"/></svg></div><p class="card-desc">Lorem ipsum dolor sit amet</p><div class="card-price"><b>$32.99</b><span class="swatches"><i style="background:#1d1d1d"></i><i style="background:#f2f0ed;border:1px solid #ccc"></i><i style="background:#d8d8d8"></i></span></div></article>
    <article class="card"><div class="card-photo" role="img" aria-label="Model in a white shirt and trousers" style="background:linear-gradient(160deg,#e4e0db,#f6f4f1 50%,#d2ccc5)"></div><div class="card-name">Product Name<svg viewBox="0 0 20 20"><path d="M10 17s-7-4.3-7-9a4 4 0 0 1 7-2.5A4 4 0 0 1 17 8c0 4.7-7 9-7 9z"/></svg></div><p class="card-desc">Lorem ipsum dolor sit amet</p><div class="card-price"><b>$32.99</b><span class="swatches"><i style="background:#1d1d1d"></i><i style="background:#f6f4f1;border:1px solid #ccc"></i><i style="background:#d8d8d8"></i></span></div></article>
    <article class="card"><div class="card-photo" role="img" aria-label="Model in a camel blazer" style="background:linear-gradient(160deg,#c7ae94,#a07f60 50%,#d6c4b0)"><span class="badge">20% OFF</span></div><div class="card-name">Product Name<svg viewBox="0 0 20 20"><path d="M10 17s-7-4.3-7-9a4 4 0 0 1 7-2.5A4 4 0 0 1 17 8c0 4.7-7 9-7 9z"/></svg></div><p class="card-desc">Lorem ipsum dolor sit amet</p><div class="card-price"><b>$32.99</b><span class="swatches"><i style="background:#1d1d1d"></i><i style="background:#a07f60"></i><i style="background:#d8d8d8"></i></span></div></article>

    <article class="card"><div class="card-photo" role="img" aria-label="Model in a white knit sweater dress" style="background:linear-gradient(160deg,#d8d2cc,#f1ede8 50%,#c9c0b7)"><span class="badge">20% OFF</span></div><div class="card-name">Product Name<svg viewBox="0 0 20 20"><path d="M10 17s-7-4.3-7-9a4 4 0 0 1 7-2.5A4 4 0 0 1 17 8c0 4.7-7 9-7 9z"/></svg></div><p class="card-desc">Lorem ipsum dolor sit amet</p><div class="card-price"><b>$32.99</b><span class="swatches"><i style="background:#1d1d1d"></i><i style="background:#c9a27a"></i><i style="background:#d8d8d8"></i></span></div></article>
    <article class="card"><div class="card-photo" role="img" aria-label="Model in a beige oversized sweater" style="background:linear-gradient(160deg,#d9d2c9,#c4ab8f 50%,#e3ddd6)"></div><div class="card-name">Product Name<svg viewBox="0 0 20 20"><path d="M10 17s-7-4.3-7-9a4 4 0 0 1 7-2.5A4 4 0 0 1 17 8c0 4.7-7 9-7 9z"/></svg></div><p class="card-desc">Lorem ipsum dolor sit amet</p><div class="card-price"><b>$32.99</b><span class="swatches"><i style="background:#1d1d1d"></i><i style="background:#c4ab8f"></i><i style="background:#d8d8d8"></i></span></div></article>
    <article class="card"><div class="card-photo" role="img" aria-label="Model in a rust polka dot blouse" style="background:linear-gradient(160deg,#d3c3b1,#a75a2e 50%,#c9b39b)"></div><div class="card-name">Product Name<svg viewBox="0 0 20 20"><path d="M10 17s-7-4.3-7-9a4 4 0 0 1 7-2.5A4 4 0 0 1 17 8c0 4.7-7 9-7 9z"/></svg></div><p class="card-desc">Lorem ipsum dolor sit amet</p><div class="card-price"><b>$32.99</b><span class="swatches"><i style="background:#1d1d1d"></i><i style="background:#a75a2e"></i><i style="background:#d8d8d8"></i></span></div></article>
    <article class="card"><div class="card-photo" role="img" aria-label="Model in an olive knit top" style="background:linear-gradient(160deg,#4a2c22,#5c5a3e 50%,#3a241c)"><span class="badge">NEW</span></div><div class="card-name">Product Name<svg viewBox="0 0 20 20"><path d="M10 17s-7-4.3-7-9a4 4 0 0 1 7-2.5A4 4 0 0 1 17 8c0 4.7-7 9-7 9z"/></svg></div><p class="card-desc">Lorem ipsum dolor sit amet</p><div class="card-price"><b>$32.99</b><span class="swatches"><i style="background:#1d1d1d"></i><i style="background:#5c5a3e"></i><i style="background:#d8d8d8"></i></span></div></article>

    <article class="card"><div class="card-photo" role="img" aria-label="Model in a printed mini dress" style="background:linear-gradient(160deg,#d7d3ce,#6e6a66 50%,#cfc9c2)"><span class="badge">20% OFF</span></div><div class="card-name">Product Name<svg viewBox="0 0 20 20"><path d="M10 17s-7-4.3-7-9a4 4 0 0 1 7-2.5A4 4 0 0 1 17 8c0 4.7-7 9-7 9z"/></svg></div><p class="card-desc">Lorem ipsum dolor sit amet</p><div class="card-price"><b>$32.99</b><span class="swatches"><i style="background:#1d1d1d"></i><i style="background:#6e6a66"></i><i style="background:#d8d8d8"></i></span></div></article>
    <article class="card"><div class="card-photo" role="img" aria-label="Model in a white dotted summer dress" style="background:linear-gradient(160deg,#e6e2dd,#f5f3f0 50%,#c8c1ba)"></div><div class="card-name">Product Name<svg viewBox="0 0 20 20"><path d="M10 17s-7-4.3-7-9a4 4 0 0 1 7-2.5A4 4 0 0 1 17 8c0 4.7-7 9-7 9z"/></svg></div><p class="card-desc">Lorem ipsum dolor sit amet</p><div class="card-price"><b>$32.99</b><span class="swatches"><i style="background:#1d1d1d"></i><i style="background:#f5f3f0;border:1px solid #ccc"></i><i style="background:#d8d8d8"></i></span></div></article>
    <article class="card"><div class="card-photo" role="img" aria-label="Model in a red satin slip dress" style="background:linear-gradient(160deg,#ece8e4,#8e1f26 50%,#e6e1dc)"></div><div class="card-name">Product Name<svg viewBox="0 0 20 20"><path d="M10 17s-7-4.3-7-9a4 4 0 0 1 7-2.5A4 4 0 0 1 17 8c0 4.7-7 9-7 9z"/></svg></div><p class="card-desc">Lorem ipsum dolor sit amet</p><div class="card-price"><b>$32.99</b><span class="swatches"><i style="background:#1d1d1d"></i><i style="background:#8e1f26"></i><i style="background:#d8d8d8"></i></span></div></article>
    <article class="card"><div class="card-photo" role="img" aria-label="Model in a camel blazer" style="background:linear-gradient(160deg,#c7ae94,#a07f60 50%,#d6c4b0)"><span class="badge">20% OFF</span></div><div class="card-name">Product Name<svg viewBox="0 0 20 20"><path d="M10 17s-7-4.3-7-9a4 4 0 0 1 7-2.5A4 4 0 0 1 17 8c0 4.7-7 9-7 9z"/></svg></div><p class="card-desc">Lorem ipsum dolor sit amet</p><div class="card-price"><b>$32.99</b><span class="swatches"><i style="background:#1d1d1d"></i><i style="background:#a07f60"></i><i style="background:#d8d8d8"></i></span></div></article>
  </div>
</section>

<div class="load-more">LOAD MORE</div>

<section class="newsletter">
  <h2>Sign For Newsletter</h2>
  <p>We will send you the good stuff, including $10 off your first order.</p>
  <div class="signup"><span>Email Address</span><b>SUBSCRIBE</b></div>
</section>

<footer class="site-footer">
  <div class="footer-brand"><span class="brand-name">LUNE</span></div>
  <div class="footer-col" style="left:400px">
    <h3>HELP</h3>
    <ul><li>Email Address</li><li>Returns/exchanges</li><li>Delivery information</li><li>FAQ</li></ul>
  </div>
  <div class="footer-col" style="left:660px">
    <h3>SHOP</h3>
    <ul><li>Tops</li><li>Bottoms</li><li>Intimates</li><li>Dresses</li><li>Swim</li></ul>
  </div>
  <div class="footer-col social" style="left:940px">
    <h3>FOLLOW US</h3>
    <ul><li><i></i>Pagebook</li><li><i></i>Chirper</li><li><i></i>Snapgram</li><li><i></i>Worknet</li></ul>
  </div>
  <div class="legal">Terms &amp; Conditions, Privacy Policy and @2021 Followed by lune</div>
</footer>

</body>
</html>
```